Wren of Fabrics relaunch: brand, logo and website redesign

Wren of Fabrics www.wrenoffabrics.com is relaunching to focus on empowering style advice, e books and courses.
We need a new logo, brand identity and website which reflects this change.
The structure of the site and pages have been completed http://dev1.wrenoffabrics.com/
but we need to update the brand look and feel
Please read the full brief, uploaded, before submitting your designs.

Target Market(s)

Women, primarily aged 28-45, English speaking USA and UK
Ambitious and determined. Looking for solutions. Open to self-improvement.
Maybe not as confident with style and body image as other parts of their life.

Logo Text

Brand name Wren of Fabrics Strapline version 1: Unlock your personal best Strapline version 2: Unlock better Logo/graphical icon for use with/without text

Number of Pages Required

3 page

Font styles to use
Sans Serif

Requirements
Must have
• 1. Web designs for home page, a channel page and advice page (see attached brief)
Web designs must be consistent with new website design navigation, and page structure http://dev1.wrenoffabrics.com/
2. Web style guide to include colour palettes/system; web fonts, icons, illustrations and guidelines/examples free stock photography. see Mindmap upload for example of colour pallette we like.
Nice to have
• Ebook front covers
Quiz promotions
Course promotions
Other web pages
Social media pages eg Pagebook, Snapgrid,Chirpline
Should not have
• Paid photography or photos where don’t have the rights

```html
<!DOCTYPE html>
<html lang="en">
<head>
<meta charset="utf-8">
<title>Colour Palette</title>
<link rel="stylesheet" href="https://fonts.googleapis.com/css2?family=Tenor+Sans&family=Poiret+One&display=swap">
<style>
  :root {
    --paper: #ffffff;
    --ink-navy: #14264a;
    --label-ink: #ffffff;
    --primary-orange: #fd8129;
    --secondary-red: #fb4a4a;
    --secondary-yellow: #ffd83b;
    --secondary-green: #29e254;
    --secondary-purple: #b159c6;
    --accent-dot: #29e254;
  }
  * { margin: 0; padding: 0; box-sizing: border-box; }
  html, body {
    width: 1200px;
    height: 772px;
    overflow: hidden;
    background: var(--paper);
  }
  .palette-sheet {
    position: relative;
    width: 1200px;
    height: 772px;
    background: var(--paper);
  }
  .section-title {
    position: absolute;
    top: 187px;
    font-family: "Tenor Sans", sans-serif;
    font-weight: 400;
    font-size: 36px;
    line-height: 1;
    color: var(--ink-navy);
    white-space: nowrap;
    transform: scaleX(0.86);
    transform-origin: left top;
  }
  .section-title--primary { left: 211px; }
  .section-title--secondary { left: 609px; }

  .swatch {
    position: absolute;
    display: flex;
    align-items: center;
    justify-content: center;
  }
  .swatch__code {
    font-family: "Poiret One", sans-serif;
    color: var(--label-ink);
    line-height: 1;
    white-space: nowrap;
  }
  .swatch--primary {
    left: 212.5px;
    top: 266.5px;
    width: 323px;
    height: 323px;
    background: var(--primary-orange);
  }
  .swatch--primary .swatch__code { font-size: 21px; }

  .swatch--small { width: 148px; height: 148px; }
  .swatch--small .swatch__code { font-size: 12px; }

  .swatch--red    { left: 612.5px; top: 268px;   background: var(--secondary-red); }
  .swatch--yellow { left: 792px;   top: 268px;   background: var(--secondary-yellow); }
  .swatch--green  { left: 612.5px; top: 439.5px; background: var(--secondary-green); }
  .swatch--purple { left: 792px;   top: 439.5px; background: var(--secondary-purple); }

  .swatch--yellow .swatch__code { transform: translate(7px, -2px); }
  .swatch--green .swatch__code { transform: translateX(-1px); }

  .corner-dot {
    position: absolute;
    left: 64.5px;
    top: 750.5px;
    width: 4px;
    height: 4px;
  }
</style>
</head>
<body>
  <main class="palette-sheet">
    <h2 class="section-title section-title--primary">Primary Color</h2>
    <h2 class="section-title section-title--secondary">Secondary Color</h2>

    <div class="swatch swatch--primary"><span class="swatch__code">#FD8129</span></div>

    <div class="swatch swatch--small swatch--red"><span class="swatch__code">#FB4A4A</span></div>
    <div class="swatch swatch--small swatch--yellow"><span class="swatch__code">#FFD83B</span></div>
    <div class="swatch swatch--small swatch--green"><span class="swatch__code">#29E254</span></div>
    <div class="swatch swatch--small swatch--purple"><span class="swatch__code">#B159C6</span></div>

    <svg class="corner-dot" viewBox="0 0 4 4" aria-hidden="true">
      <circle cx="2" cy="2" r="1.6" fill="var(--accent-dot)"/>
    </svg>
  </main>
</body>
</html>
```